Brightway Haus Inc. Business Card Design

Brightway Haus Inc. is in search of a great clean design for our business cards!

Looking to incorporate our full logo and watermark on side one (however, I am open to having the text and watermark separated within the design.)

On side two, I am looking to have contact information (Name, Position, Phone #, Email, Website (www.thebrightwayhaus.ca). Can have the logo and/or watermark as part of the design if applicable.

Please add tagline "Where Shine Counts" on either side 1 or 2. This tagline can be in a sans serif, serif or cursive font as long as it compliments overall design. Capitalization can be title or sentence case depending on how it fits within the design.

Get creative!! Looking for a clean, crisp, premium design! Looking for a glossy card finish with spot UV features when printed. Cards will also be printed with rounded corners. Standard dimensions (3.5 x 2).

Target Market(s)

B2B - primary clients are business owners or property management corporations. (residential jobs are few and far between)

Industry/Entity Type

Business

Contact Information for Business Card

- clean, crisp design
- double sided
- spot UV accents and glossy finish upon printing
- standard business card size (3.5 x 2) with rounded corners
- please see project description for requirements per side

Font styles to use
Sans Serif

Requirements
Must have
• - adequate bleeds with print ready files
• - cohesive design elements between side 1 & 2
• - spot UV elements (can be on both sides or just one, use your discretion)
• - colour pallet should match the logo file provided
• - incorporate tagline "where shine counts" (this tagline can be in a serif or sans serif font as long as it is complimentary to the overall design.
Nice to have
• - Premium elements with a clean design
Should not have
• - Please omit cartoon or whimsical like designs, think premium.
• - Colours should not stray from the pallet of the provided logo.

```html
<!DOCTYPE html>
<html lang="en">
<head>
<meta charset="utf-8">
<title>Brightway Haus Inc. Business Card</title>
<link href="https://fonts.googleapis.com/css2?family=Roboto:ital,wght@0,400;0,500;0,700;1,400&display=swap" rel="stylesheet">
<style>
  :root {
    --stage: #2b2b2b;
    --paper: #f4f4f4;
    --teal: #0fb3b5;
    --navy: #1f2a55;
    --ink: #4a4a4a;
    --rule: #9a9a9a;
    --white: #ffffff;
  }
  html, body {
    margin: 0;
    padding: 0;
    width: 1200px;
    height: 960px;
    overflow: hidden;
    background: var(--stage);
    font-family: "Roboto", Arial, sans-serif;
  }
  .canvas {
    position: relative;
    width: 1200px;
    height: 960px;
  }
  .card {
    position: absolute;
    width: 600px;
    height: 341px;
    border-radius: 20px;
    overflow: hidden;
  }
  /* front side */
  .card-front {
    left: 314px;
    top: 114px;
    background: var(--paper);
  }
  .card-front .edge-line {
    position: absolute;
    left: 0; right: 0;
    top: 322px;
    height: 2px;
    background: var(--navy);
  }
  .card-front .edge-band {
    position: absolute;
    left: 0; right: 0;
    top: 324px;
    bottom: 0;
    background: var(--teal);
  }
  .brand {
    position: absolute;
    left: 48px;
    top: 155px;
    display: flex;
    align-items: center;
    gap: 8px;
  }
  .brand-square {
    width: 20px;
    height: 20px;
    background: var(--teal);
  }
  .brand-name {
    font-weight: 700;
    font-size: 22px;
    color: var(--navy);
    letter-spacing: 0.2px;
    white-space: nowrap;
  }
  .divider {
    position: absolute;
    left: 325px;
    top: 72px;
    width: 2px;
    height: 205px;
    background: linear-gradient(to bottom, transparent, var(--rule) 15%, var(--rule) 85%, transparent);
  }
  .contact {
    position: absolute;
    left: 356px;
    top: 70px;
    color: var(--ink);
  }
  .contact-name {
    margin: 0;
    font-size: 20px;
    font-weight: 500;
    color: var(--teal);
    line-height: 26px;
  }
  .contact-role {
    margin: 0 0 18px;
    font-size: 15px;
    font-weight: 500;
    color: var(--navy);
    line-height: 20px;
  }
  .contact-address {
    margin: 0 0 12px;
    font-style: normal;
    font-size: 14px;
    line-height: 19px;
  }
  .contact-list {
    list-style: none;
    margin: 0;
    padding: 0;
    font-size: 14px;
    line-height: 19px;
  }
  .contact-list li {
    display: flex;
    align-items: center;
    gap: 9px;
  }
  .contact-list svg {
    width: 13px;
    height: 13px;
    fill: var(--teal);
    flex: none;
  }
  /* back side */
  .card-back {
    left: 311px;
    top: 472px;
    height: 342px;
    background: var(--teal);
    color: var(--white);
  }
  .back-brand {
    position: absolute;
    left: 0; right: 0;
    top: 120px;
    display: flex;
    justify-content: center;
    align-items: center;
    gap: 12px;
  }
  .back-brand .brand-square {
    width: 30px;
    height: 30px;
    background: var(--white);
  }
  .back-brand .brand-name {
    font-size: 34px;
    color: var(--white);
  }
  .tagline {
    position: absolute;
    left: 0; right: 0;
    top: 280px;
    display: flex;
    justify-content: center;
    align-items: center;
    gap: 6px;
    font-style: italic;
    font-size: 19px;
  }
  .tagline::before, .tagline::after {
    content: "";
    width: 104px;
    height: 1px;
  }
  .tagline::before { background: linear-gradient(to right, transparent, var(--white)); }
  .tagline::after { background: linear-gradient(to left, transparent, var(--white)); }
</style>
</head>
<body>
<main class="canvas">
  <section class="card card-front" aria-label="Business card front">
    <div class="brand">
      <span class="brand-square"></span>
      <span class="brand-name">Brightway Haus Inc.</span>
    </div>
    <div class="divider"></div>
    <div class="contact">
      <h1 class="contact-name">DANIEL MERCER</h1>
      <p class="contact-role">CEO/FOUNDER</p>
      <address class="contact-address">1420 Harbour Crest Road<br>Vancouver, BC V6B 2K4</address>
      <ul class="contact-list">
        <li><svg viewBox="0 0 16 16" aria-hidden="true"><path d="M3.5 1 6 3.5 4.6 5.6c.9 2.2 3.5 4.9 5.8 5.8L12.5 10 15 12.5 13.3 15C7 14.5 1.5 9 1 2.7z"/></svg>604 555 0182</li>
        <li><svg viewBox="0 0 16 16" aria-hidden="true"><path d="M4 0h8a1 1 0 0 1 1 1v14a1 1 0 0 1-1 1H4a1 1 0 0 1-1-1V1a1 1 0 0 1 1-1zm1 2v10h6V2zm3 11a1 1 0 1 0 0 2 1 1 0 0 0 0-2z"/></svg>604 555 0147</li>
        <li><svg viewBox="0 0 16 16" aria-hidden="true"><path d="M4 1h8v4H4zM1 6h14v7h-3v2H4v-2H1zm4 5v3h6v-3z"/></svg>604 555 0169</li>
        <li><svg viewBox="0 0 16 16" aria-hidden="true"><path d="M1 3h14v10H1zm1.5 1.2v.4L8 8.6l5.5-4V4.2zM2.5 6.4V12h11V6.4L8 10.3z"/></svg>hello@thebrightwayhaus.ca</li>
        <li><svg viewBox="0 0 16 16" aria-hidden="true"><path d="M8 1a7 7 0 1 0 0 14A7 7 0 0 0 8 1zm0 1.5c.9 0 1.9 1.7 2.2 4.5H5.8C6.1 4.2 7.1 2.5 8 2.5zM2.6 8.5h1.7c.1 1.7.4 3.2 1 4.3A5.5 5.5 0 0 1 2.6 8.5zm0-1.5a5.5 5.5 0 0 1 2.7-3.8c-.6 1.1-.9 2.6-1 3.8zm3.2 1.5h4.4c-.3 2.8-1.3 5-2.2 5s-1.9-2.2-2.2-5zm5.9 0h1.7a5.5 5.5 0 0 1-2.7 4.3c.6-1.1.9-2.6 1-4.3zm0-1.5c-.1-1.2-.4-2.7-1-3.8A5.5 5.5 0 0 1 13.4 7z"/></svg>www.thebrightwayhaus.ca</li>
      </ul>
    </div>
    <div class="edge-line"></div>
    <div class="edge-band"></div>
  </section>

  <section class="card card-back" aria-label="Business card back">
    <div class="back-brand">
      <span class="brand-square"></span>
      <span class="brand-name">Brightway Haus Inc.</span>
    </div>
    <p class="tagline">Where Shine Counts</p>
  </section>
</main>
</body>
</html>
```